KRT Info Brochure

We need a brochure design for a new not-for-profit organisation that is aimed at providing homeless people with a residence that also provides counselling and vocational training to assist them to find suitable employment at the end of the program.
PLEASE NOTE:
Brochure to be A4.
I know the brochure is quite long, it is really a booklet, but please note that it does not have to have a lot of work done on it, I just want it to look professional and the front cover and inside page to look good.
Also please leave about 2-3 pages at the end as I will be adding in some architect drawings.
Please add in a last page with Contact written at the bottom - we will fill that in later. So please ensure it is editable in PDF.
Thank you so much.
Cheers
Marta

```html
<!DOCTYPE html>
<html lang="en">
<head>
<meta charset="utf-8">
<title>KRT Info Brochure – Inside Spread</title>
<link rel="stylesheet" href="https://fonts.googleapis.com/css2?family=Arimo:wght@400;700&display=swap">
<style>
  :root {
    --olive: #8d8d3b;
    --olive-dark: #6f7029;
    --gold: #e9b64a;
    --cream: #ece2a4;
    --leaf: #d5dfa6;
    --leaf-light: #eef2d8;
    --ink: #2b2b2b;
    --heading: #7d8030;
    --paper: #ffffff;
    --backdrop: #e4e4e4;
    --photo-a: #c9ced3;
    --photo-b: #8e9aa6;
  }
  * { margin: 0; padding: 0; box-sizing: border-box; }
  html, body { width: 1200px; height: 847px; overflow: hidden; }
  body {
    background: var(--backdrop);
    font-family: "Arimo", Arial, sans-serif;
    color: var(--ink);
    position: relative;
  }
  .spread {
    position: absolute;
    left: 40px; top: 44px;
    width: 1120px; height: 760px;
    display: flex;
    box-shadow: 0 6px 24px rgba(0,0,0,.18);
  }
  .page {
    position: relative;
    width: 560px; height: 760px;
    background: var(--paper);
    overflow: hidden;
  }
  .page-art { position: absolute; left: 0; top: 0; }
  .web-address {
    position: absolute;
    color: #fff;
    font-size: 10px;
    letter-spacing: .2px;
  }
  .page--left .web-address { left: 30px; top: 36px; }
  .page--right .web-address { left: 150px; bottom: 40px; }

  .section-title {
    color: var(--heading);
    font-weight: 700;
    font-size: 15px;
    line-height: 1.2;
    margin-bottom: 3px;
  }
  .body-text { font-size: 9.5px; line-height: 1.28; margin-bottom: 5px; }

  .page--left .content { position: absolute; left: 30px; top: 96px; width: 500px; }

  .staff-block { display: flex; gap: 14px; margin: 5px 0 8px; }
  .staff-table { width: 250px; border-collapse: collapse; font-size: 8px; line-height: 1; }
  .staff-table th {
    background: var(--olive);
    color: #fff;
    font-weight: 400;
    height: 15px;
    font-size: 9.5px;
  }
  .staff-table td { height: 10px; padding: 0 4px; border-bottom: 1px solid #fff; white-space: nowrap; }
  .staff-table .group {
    background: var(--cream);
    font-size: 10px;
    line-height: 1.2;
    width: 72px;
    white-space: normal;
    border-right: 2px solid #fff;
  }
  .staff-table tr:nth-child(odd) td.role { background: var(--leaf); }
  .staff-table tr:nth-child(even) td.role { background: var(--leaf-light); }

  .staff-photos { display: flex; flex-direction: column; gap: 10px; }
  .photo { display: block; }
  .photo--meeting { width: 200px; height: 102px; background: linear-gradient(135deg, #e8e8ea, #b9bcc2); }
  .photo--finance { width: 200px; height: 100px; background: linear-gradient(135deg, #f0f0f0, #b7b3a6); }

  .sustain-block { display: flex; gap: 12px; }
  .sustain-text { width: 310px; }
  .eco-list { font-size: 9.5px; line-height: 1.22; margin: 2px 0 5px 26px; }
  .photo--plant { width: 150px; height: 112px; margin-top: 4px; background: radial-gradient(circle at 50% 45%, #6f8d3a, #4a3a2a 60%, #2a2420); }

  .page--right .content { position: absolute; left: 70px; top: 318px; width: 460px; }
  .page--right .section-title { margin-top: 8px; }
</style>
</head>
<body>
<main class="spread">

  <section class="page page--left">
    <svg class="page-art" width="560" height="760" viewBox="0 0 560 760" aria-hidden="true">
      <path d="M0 0 H560 V60 C420 90 200 50 0 86 Z" fill="var(--olive)"/>
      <path d="M0 92 C200 56 420 96 560 66" fill="none" stroke="var(--gold)" stroke-width="3"/>
      <path d="M0 760 H560 V672 C380 712 180 666 0 698 Z" fill="var(--olive)"/>
      <path d="M0 688 C180 656 380 708 560 662" fill="none" stroke="var(--gold)" stroke-width="3"/>
    </svg>
    <p class="web-address">www.KRThomefoundation.org</p>

    <div class="content">
      <h2 class="section-title">3.4. KRT Staff</h2>
      <p class="body-text">It is expected that KRT will employ 17 staff (in addition to the CEO), including 4 onsite staff. It is expected that a full contingent of staff will not be required until the facility reaches full capacity. In addition to specialist staff, KRT will seek the services of volunteers to assist with training and medical requirements (eg. Chiropractor, massage therapist etc).</p>

      <div class="staff-block">
        <table class="staff-table">
          <tr><th colspan="2">Staff Requirements</th></tr>
          <tr><td class="group" rowspan="5">Counselling Staff</td><td class="role">Senior Psychologist</td></tr>
          <tr><td class="role">Psychologist Intern</td></tr>
          <tr><td class="role">Counsellors x 2</td></tr>
          <tr><td class="role">Residential Mentor x 2 (onsite)</td></tr>
          <tr><td class="role">Case Workers x 2</td></tr>
          <tr><td class="group" rowspan="9">Admin Staff</td><td class="role">Operations Manager</td></tr>
          <tr><td class="role">Personal Assistant</td></tr>
          <tr><td class="role">Information Technology Manager/Trainer</td></tr>
          <tr><td class="role">H.R. Manager</td></tr>
          <tr><td class="role">Marketing/Promotions Manager</td></tr>
          <tr><td class="role">Office Manager</td></tr>
          <tr><td class="role">Administration Assistant x 2</td></tr>
          <tr><td class="role">Training Co-ordinator</td></tr>
          <tr><td class="role">Book Keeper (Part time)</td></tr>
          <tr><td class="group" rowspan="6">General Staff</td><td class="role">Cooks x 2</td></tr>
          <tr><td class="role">Barista</td></tr>
          <tr><td class="role">Grounds Person x 2</td></tr>
          <tr><td class="role">Facility Supervisor (onsite)</td></tr>
          <tr><td class="role">Night guard (onsite)</td></tr>
        </table>
        <div class="staff-photos">
          <div class="photo photo--meeting" role="img" aria-label="Photo: counsellor in a consultation meeting"></div>
          <div class="photo photo--finance" role="img" aria-label="Photo: hands working with a calculator and stacks of coins"></div>
        </div>
      </div>

      <h2 class="section-title">3.5. Self-Sustainment</h2>
      <p class="body-text">As previously mentioned, KRT aims to be as self-sustaining as possible in an attempt to reduce the environmental footprint of KRT and the on-going costs. Below is a list of some of the environmentally friendly / self-sustaining options KRT plans to implement. These self-sustaining options will also be used in the complementary businesses through publications and workshops.</p>
      <div class="sustain-block">
        <div class="sustain-text">
          <ul class="eco-list">
            <li>Solar and wind power</li>
            <li>Rainwater tanks</li>
            <li>Environmentally friendly insulation</li>
            <li>Grey water tanks</li>
            <li>Sewerage - worm farm waste system</li>
            <li>Organic fruit, vegetable and flower farm</li>
            <li>Fish farm system</li>
            <li>Chicken coop recycling/compost</li>
          </ul>
          <p class="body-text">The long-term aim is to bring tourist to the site, using the self-sustaining aspect of the complex, where there will be an on-site coffee shop and gallery; we believe that the self-sustainment project may also interest the environmental sector.</p>
        </div>
        <div class="photo photo--plant" role="img" aria-label="Photo: cupped hands holding soil with a young seedling"></div>
      </div>
    </div>
  </section>

  <section class="page page--right">
    <svg class="page-art" width="560" height="760" viewBox="0 0 560 760" role="img" aria-label="Photo: business team meeting around a glass table">
      <defs>
        <linearGradient id="team-photo" x1="0" y1="0" x2="1" y2="1">
          <stop offset="0" stop-color="var(--photo-a)"/>
          <stop offset="1" stop-color="var(--photo-b)"/>
        </linearGradient>
      </defs>
      <path d="M0 0 H560 V40 C400 60 200 30 0 60 Z" fill="var(--olive)"/>
      <path d="M0 52 C200 26 400 54 560 34 V270 C420 300 220 250 0 300 Z" fill="url(#team-photo)"/>
      <path d="M0 304 C220 254 420 304 560 276" fill="none" stroke="var(--gold)" stroke-width="3"/>
      <path d="M0 760 H560 V600 C420 660 200 610 0 680 Z" fill="var(--olive)"/>
      <path d="M0 670 C200 604 420 652 560 592" fill="none" stroke="var(--gold)" stroke-width="3"/>
    </svg>

    <div class="content">
      <h2 class="section-title">3.6. Timeframes</h2>
      <p class="body-text">It is envisaged that it will be 18 to 24 months from the initial funding to taking the first Residents. The KRT Management Committee will commence immediately upon funding approval.</p>
      <p class="body-text">There are three blocks of land that have been identified in the Sunshine Coast Hinterland. All three have been cleared and building could commence in a relatively short space of time.</p>

      <h2 class="section-title">3.7. Marketing and Publicity</h2>
      <p class="body-text">There are numerous opportunities for marketing and publicity. As previously mentioned, upon funding confirmation, Home Builds Today will be approached to cover the initial building. It is expected that Professionals, trade persons and suppliers will provide assistance at reduced costs in an endeavour to raise their own profile.</p>
      <p class="body-text">In addition, it is envisaged that KRT will pitch the idea of a reality TV / documentary to cover the development of the complex, the intake of the initial Residents through to the 'graduation' of the Clients. This could potentially provide significant funding for the program.</p>
      <p class="body-text">Furthermore, the KRT program will also approach morning TV shows and current affairs programs in a bid to raise awareness of the program.</p>
    </div>
    <p class="web-address">www.KRThomefoundation.org</p>
  </section>

</main>
</body>
</html>
```